Elevating our current Business Card Design

We want to elevate our current business card with a new design to look like a zenith 300 company. We are a premium lubricant distributor (oil and grease).
We need 2 versions, version 1 is as per the uploaded a copy of our current business card with the English version.
For our Chinese version we need to use the front to be English in English and have the back of the card designed exactly like the front for all info to be in Chinese.
The design template needs to be such that we can amend the template with adding different information for each person's card.
The background colour of the card can be changed- we just need to clearly see all information on the card and logos.
The QJR and Ember steady logos cannot have any colour or display changes- only use the logos attached.
All logos need to be included and all information from the attached current card

```html
<!DOCTYPE html>
<html lang="en">
<head>
<meta charset="utf-8">
<title>Orvanta Business Card</title>
<link href="https://fonts.googleapis.com/css2?family=Open+Sans:ital,wght@0,400;0,600;0,700;0,800;1,700&display=swap" rel="stylesheet">
<style>
  :root {
    --page: #e6e2dc;
    --card: #ece4d6;
    --green-light: #24503f;
    --green-dark: #08281a;
    --red: #c8161c;
    --red-deep: #8e1016;
    --orange: #e07a2a;
    --gold: #d49a1e;
    --ink: #2a2a2a;
    --contact: #d9d2c4;
    --badge: #7c7a76;
    --badge-accent: #e66a1c;
  }
  html, body {
    margin: 0;
    width: 1200px;
    height: 1046px;
    overflow: hidden;
    background: var(--page);
    font-family: "Open Sans", Arial, sans-serif;
  }
  .card {
    position: absolute;
    left: 60px;
    top: 229px;
    width: 1080px;
    height: 588px;
    border-radius: 28px;
    overflow: hidden;
    background: var(--card);
    box-shadow: 0 10px 30px rgba(0,0,0,0.18);
  }
  .card-art { position: absolute; inset: 0; }
  .holder { position: absolute; left: 45px; top: 36px; }
  .holder-name {
    margin: 0;
    font-size: 43px;
    font-weight: 700;
    font-style: italic;
    color: var(--red);
    line-height: 1.1;
  }
  .holder-role {
    margin: 0 0 0 4px;
    font-size: 26px;
    font-weight: 600;
    color: var(--ink);
    letter-spacing: 0.5px;
  }
  .brand-mark {
    position: absolute;
    left: 560px;
    top: 100px;
    width: 480px;
    display: flex;
    align-items: center;
    gap: 16px;
  }
  .brand-dot {
    flex: 0 0 50px;
    width: 50px; height: 50px;
    border-radius: 50%;
    background: var(--gold);
  }
  .brand-name {
    font-size: 78px;
    font-weight: 800;
    color: var(--red);
    letter-spacing: -1px;
    line-height: 1;
    white-space: nowrap;
  }
  .address {
    position: absolute;
    left: 45px;
    top: 274px;
    margin: 0;
    font-size: 25px;
    line-height: 35px;
    color: var(--contact);
    font-style: normal;
  }
  .contacts {
    position: absolute;
    left: 40px;
    top: 370px;
    margin: 0;
    padding: 0;
    list-style: none;
  }
  .contacts li {
    display: flex;
    align-items: center;
    height: 35.5px;
    font-size: 26px;
    color: var(--contact);
  }
  .contacts svg { width: 24px; height: 24px; margin-right: 20px; flex: 0 0 24px; }
  .badges {
    position: absolute;
    left: 650px;
    top: 418px;
    display: flex;
    gap: 34px;
    align-items: center;
  }
  .badge-plain {
    width: 62px; height: 62px;
    border-radius: 50%;
    border: 6px solid var(--badge);
    box-sizing: border-box;
    display: flex; align-items: center; justify-content: center;
  }
  .badge-plain span {
    width: 30px; height: 30px; border-radius: 50%;
    background: var(--badge-accent);
  }
  .badge-wide {
    width: 90px; height: 56px;
    border-radius: 30px 30px 6px 6px;
    background: var(--contact);
  }
  .partner-strip {
    position: absolute;
    left: 633px;
    top: 491px;
    width: 404px;
    height: 60px;
    display: flex;
    transform: skewX(-8deg);
    border: 2px solid var(--red);
    box-sizing: border-box;
  }
  .partner-own, .partner-supplier {
    display: flex; align-items: center; justify-content: center;
    font-weight: 700;
  }
  .partner-own {
    width: 52%;
    background: #ebe5db;
    color: var(--red);
    font-size: 24px;
  }
  .partner-supplier {
    width: 48%;
    background: var(--red);
    color: #ffffff;
    font-size: 24px;
  }
  .partner-own span, .partner-supplier span { transform: skewX(8deg); }
</style>
</head>
<body>
<main class="card">
  <svg class="card-art" viewBox="0 0 1080 588" width="1080" height="588" aria-hidden="true">
    <defs>
      <radialGradient id="greenField" cx="0.25" cy="0.75" r="0.9">
        <stop offset="0" stop-color="var(--green-light)"/>
        <stop offset="1" stop-color="var(--green-dark)"/>
      </radialGradient>
      <linearGradient id="orangeFade" x1="0" x2="1">
        <stop offset="0" stop-color="#e07a2a"/>
        <stop offset="1" stop-color="#e07a2a" stop-opacity="0"/>
      </linearGradient>
    </defs>
    <path d="M0 187 C 250 150, 450 235, 640 360 C 780 445, 950 420, 1080 300 L1080 588 L0 588 Z" fill="url(#greenField)"/>
    <path d="M40 170 C 260 140, 460 218, 650 345 C 790 430, 950 410, 1080 285" fill="none" stroke="#a3161a" stroke-width="12"/>
    <path d="M0 162 C 140 132, 300 135, 430 178" fill="none" stroke="url(#orangeFade)" stroke-width="14"/>
    <path d="M700 308 C 850 362, 985 335, 1080 245" fill="none" stroke="#d49a1e" stroke-width="6"/>
  </svg>

  <header class="holder">
    <h1 class="holder-name">Maren Vostic</h1>
    <p class="holder-role">Administration Executive</p>
  </header>

  <div class="brand-mark">
    <span class="brand-dot"></span>
    <span class="brand-name">ORVANTA</span>
  </div>

  <address class="address">48 Depot Crescent<br>Harlow Park, WA 6142</address>

  <ul class="contacts">
    <li><svg viewBox="0 0 24 24"><path d="M6 3 L9 3 L10 8 L8 10 C9 13 11 15 14 16 L16 14 L21 15 L21 18 C21 20 19 21 17 21 C10 20 4 14 3 7 C3 5 4 3 6 3 Z" fill="#c8161c"/></svg>1300 472 816</li>
    <li><svg viewBox="0 0 24 24"><rect x="6" y="2" width="12" height="20" rx="2" fill="none" stroke="#c8161c" stroke-width="2"/><circle cx="12" cy="18" r="1.2" fill="#c8161c"/></svg>+61 421 607 394</li>
    <li><svg viewBox="0 0 24 24"><rect x="2" y="9" width="20" height="12" rx="2" fill="#c8161c"/><rect x="7" y="3" width="10" height="7" fill="#c8161c"/></svg>+61 8 9527 4410</li>
    <li><svg viewBox="0 0 24 24"><circle cx="12" cy="12" r="10" fill="#c8161c"/><path d="M2 12 H22 M12 2 C7 7 7 17 12 22 M12 2 C17 7 17 17 12 22" stroke="#0b2b1d" stroke-width="1.4" fill="none"/></svg>www.orvantadirect.com</li>
    <li><svg viewBox="0 0 24 24"><rect x="2" y="6" width="20" height="14" rx="2" fill="#c8161c"/><path d="M2 7 L12 14 L22 7" stroke="#0b2b1d" stroke-width="1.6" fill="none"/></svg>maren.vostic@orvantadirect.com</li>
  </ul>

  <div class="badges">
    <div class="badge-wide" role="img" aria-label="Ember steady network member badge"></div>
    <div class="badge-plain" role="img" aria-label="QJR certification badge"><span></span></div>
    <div class="badge-plain" role="img" aria-label="QJR certification badge"><span></span></div>
    <div class="badge-plain" role="img" aria-label="QJR certification badge"><span></span></div>
  </div>

  <div class="partner-strip">
    <div class="partner-own"><span>ORVANTA</span></div>
    <div class="partner-supplier"><span>KESTRAL</span></div>
  </div>
</main>
</body>
</html>
```